I need a new business card designed, we recently rebranded and I need to get a fresh design to match our new logo, colours and branding.

Details:

Derek Havill | Founder & CEO
Address: 7 Marlowfern Lane, #09-14 Tavenport Crest, Singapore 318547
Tel: +65 93568214
Web: www.frostkarta.com.sg
hello@frostkarta.com.sg

I've attached my old card as well

Industry/Entity Type

Business

Requirements
Must have
• Front and Back
Interesting use of logo
Correct use of colour scheme

```html
<!DOCTYPE html>
<html lang="en">
<head>
<meta charset="utf-8">
<title>frostkarta business card</title>
<link href="https://fonts.googleapis.com/css2?family=Didact+Gothic&display=swap" rel="stylesheet">
<style>
  :root {
    --backdrop: #3b2a20;
    --card-light: #ffffff;
    --card-shade: #e4e4e6;
    --ink: #5d4e48;
    --accent: #2b93c8;
    --accent-deep: #3d8bb6;
  }
  * { margin: 0; padding: 0; box-sizing: border-box; }
  html, body {
    width: 1200px;
    height: 900px;
    overflow: hidden;
    background: var(--backdrop);
    font-family: "Didact Gothic", "Century Gothic", sans-serif;
    color: var(--ink);
  }
  .canvas {
    position: relative;
    width: 1200px;
    height: 900px;
  }
  .card {
    position: absolute;
    top: 150px;
    width: 380px;
    height: 600px;
    border-radius: 22px;
    background: linear-gradient(160deg, var(--card-light) 0%, #f3f3f4 45%, var(--card-shade) 100%);
    box-shadow: 0 10px 30px rgba(0, 0, 0, 0.5);
    overflow: hidden;
  }
  .card--front { left: 180px; }
  .card--back { left: 640px; }

  /* front */
  .brand-lockup {
    position: absolute;
    left: 34px;
    bottom: 40px;
    display: flex;
    align-items: center;
    gap: 10px;
  }
  .brand-dot {
    width: 44px;
    height: 44px;
    border-radius: 50%;
    background: var(--accent);
    flex: none;
  }
  .brand-name {
    font-size: 27px;
    line-height: 1;
    color: var(--ink);
  }
  .brand-tagline {
    margin-top: 4px;
    font-size: 8px;
    letter-spacing: 0.6px;
    color: var(--accent);
    text-transform: uppercase;
  }

  /* back */
  .holder {
    position: absolute;
    top: 92px;
    left: 0;
    width: 100%;
    text-align: center;
  }
  .holder-name {
    font-size: 22px;
    letter-spacing: 0.5px;
  }
  .holder-role {
    margin-top: 8px;
    font-size: 12px;
    color: var(--accent);
  }
  .contact-list {
    position: absolute;
    top: 232px;
    left: 82px;
    list-style: none;
    font-size: 13px;
  }
  .contact-list li {
    display: flex;
    margin-bottom: 17px;
  }
  .contact-label {
    width: 22px;
    color: var(--accent);
  }
  .address {
    position: absolute;
    top: 330px;
    left: 0;
    width: 100%;
    text-align: center;
    font-size: 10px;
    line-height: 1.6;
  }
  .brand-disc {
    position: absolute;
    right: 40px;
    bottom: 60px;
    width: 140px;
    height: 140px;
    border-radius: 50%;
    background: linear-gradient(200deg, var(--accent) 0%, var(--accent-deep) 100%);
  }
</style>
</head>
<body>
  <main class="canvas">
    <section class="card card--front" aria-label="Card front">
      <div class="brand-lockup">
        <span class="brand-dot" aria-hidden="true"></span>
        <div>
          <div class="brand-name">frostkarta</div>
          <div class="brand-tagline">Web Design &amp; Consultancy</div>
        </div>
      </div>
    </section>

    <section class="card card--back" aria-label="Card back">
      <header class="holder">
        <h1 class="holder-name" style="font-weight:400">Derek Havill</h1>
        <p class="holder-role">Founder &amp; CEO</p>
      </header>
      <ul class="contact-list">
        <li><span class="contact-label">T:</span><span>+65 93568214</span></li>
        <li><span class="contact-label">W:</span><span>www.frostkarta.com.sg</span></li>
        <li><span class="contact-label">E:</span><span>hello@frostkarta.com.sg</span></li>
      </ul>
      <p class="address">7 Marlowfern Lane, #09-14 Tavenport Crest,<br>Singapore 318547</p>
      <span class="brand-disc" aria-hidden="true"></span>
    </section>
  </main>
</body>
</html>
```